Business Card for Polygraph business in Africa

Business Card . Polygraph Examiner based in Tanzania, East Africa.
Business Card will be used to disseminate contact information to potential clients.
It should convey that I am a professional specifically in the polygraph field and perform my work with integrity.

I have attached the business card that I'm currently using, which I threw together myself initially. It's not professional enough.

Target Market(s)

Banks, Accounting Firms, Government Ministries, Gas, Oil, & Gemstone Mining Concerns, Wildlife Conservation NGOs, International companies located in East Africa.

Industry/Entity Type

Business

Contact Information for Business Card

Veritrace Kilonga
Miriam Holloway
PO Box 48317
Arusha, Tanzania
+255 612 839 274
miriamholloway@postvale.example

Colors
00a990
f37122
faa54b

Requirements
Must have
• - Veritrace Kilonga (with the word "Polygraph" being more prominent than the word "Tanzania")
• - Forensic Examinations
• - Employment Screening
• - Should contain a logo of the Continental Truthline Society (of which I'm a member)
• - I would like an accent design (such as the polygraph "squiggles" of a cardio tracing or such as that)
• - My contact information (less prominent, but large enough to read legibly). I would also consider putting the contact information on the second side of the card.
Nice to have
• My color suggestions are changeable.
Should not have
• Anything "cutesy" or "cartoonish"

```html
<!DOCTYPE html>
<html lang="en">
<head>
<meta charset="utf-8">
<title>Veritrace Kilonga – Business Card</title>
<link rel="stylesheet" href="https://fonts.googleapis.com/css2?family=Roboto:wght@700&family=Work+Sans:wght@400;500&display=swap">
<style>
  :root {
    --page: #2b2b2b;
    --card-dark: #0b0b0b;
    --card-light: #ffffff;
    --navy: #1b2450;
    --ink: #3a3a3a;
    --rule: #6d6d6d;
    --white: #ffffff;
  }
  * { margin: 0; padding: 0; box-sizing: border-box; }
  html, body { width: 1200px; height: 930px; overflow: hidden; }
  body {
    background: var(--page);
    font-family: "Work Sans", sans-serif;
    position: relative;
  }
  .card {
    position: absolute;
    left: 290px;
    width: 620px;
    height: 354px;
    border-radius: 22px;
    overflow: hidden;
  }
  .card--front { top: 60px; background: var(--card-dark); }
  .card--back { top: 500px; background: var(--card-light); }

  .brand-name {
    font-family: "Roboto", sans-serif;
    font-weight: 700;
    font-size: 27px;
    letter-spacing: 0.2px;
    white-space: nowrap;
  }
  .card--front .brand-name {
    position: absolute; left: 96px; top: 170px; color: var(--white);
  }
  .member-badge {
    position: absolute; right: 64px; top: 96px;
    width: 118px; height: 118px;
    border-radius: 50%;
    background: var(--white);
    border: 6px solid var(--card-dark);
    box-shadow: 0 0 0 2px var(--white);
  }

  .card--back .brand-name {
    position: absolute; left: 40px; top: 190px; color: var(--navy);
    font-size: 24px;
  }
  .divider {
    position: absolute; left: 300px; top: 100px;
    width: 1px; height: 120px; background: var(--rule);
  }
  .contact {
    position: absolute; left: 322px; top: 92px; right: 20px;
    color: var(--ink); font-size: 14px; line-height: 1.5;
    white-space: nowrap;
  }
  .contact__name {
    font-weight: 500; font-size: 22px; color: var(--navy);
    letter-spacing: 1.5px; text-transform: uppercase; margin-bottom: 6px;
  }
  .contact__line { display: flex; align-items: center; gap: 8px; }
  .contact__line svg { width: 12px; height: 12px; flex: none; }
  .contact__line--address { padding-left: 20px; }
  .service-band {
    position: absolute; left: 0; right: 0; bottom: 0; height: 38px;
    background: var(--navy); color: var(--white);
    font-size: 14px; letter-spacing: 1px; text-transform: uppercase;
    display: flex; align-items: center; justify-content: flex-end;
    padding-right: 36px; white-space: nowrap;
  }
</style>
</head>
<body>
  <section class="card card--front" aria-label="Card front">
    <div class="brand-name">Veritrace Kilonga</div>
    <div class="member-badge" role="img" aria-label="Member badge of the Continental Truthline Society"></div>
  </section>

  <section class="card card--back" aria-label="Card back">
    <div class="brand-name">Veritrace Kilonga</div>
    <div class="divider"></div>
    <div class="contact">
      <div class="contact__name">Miriam Holloway</div>
      <div class="contact__line contact__line--address">PO Box 48317</div>
      <div class="contact__line contact__line--address">Arusha, Tanzania</div>
      <div class="contact__line">
        <svg viewBox="0 0 12 12" aria-hidden="true"><path d="M2.5 1 L4.5 1 L5.2 3.6 L4 4.6 Q5 7 7.4 8 L8.4 6.8 L11 7.5 L11 9.5 Q11 11 9.5 11 Q1 10.5 1 2.5 Q1 1 2.5 1 Z" fill="var(--navy)"/></svg>
        <span>+255 612 839 274</span>
      </div>
      <div class="contact__line">
        <svg viewBox="0 0 12 12" aria-hidden="true"><rect x="1" y="2.5" width="10" height="7" fill="none" stroke="var(--navy)" stroke-width="1.2"/><path d="M1 2.5 L6 6.5 L11 2.5" fill="none" stroke="var(--navy)" stroke-width="1.2"/></svg>
        <span>miriamholloway@postvale.example</span>
      </div>
    </div>
    <div class="service-band">Issue Investigation - Employment Screening</div>
  </section>
</body>
</html>
```